Refresh of a Media Kit for Adtech Company - Needs jazzing up!

We have a Media Kit that's too ugly and boring to send to clients. Attaching some examples of ones we like better. Keep the general styling and theme of the current media kit (it's our brand style) and all the information conveyed, but please change anything and everything else to make it more dynamic. Attaching examples of media kits we like.

The "Media Kit Vantor" is the one you're designing, the others are just examples of media kits we liked.
Updates

Here's a link to "Glamour Shots" that can be used as appropriate throughout the Media kit: https://www.filquarry.net/sh/q7mzkx31rwp8tnb/BXK4Pqwertz_LM9nVwYdQaHfZ?dl=0

Target Market(s)

Demand partners

Colors
0592cd
85cae6
34a7d8

Requirements
Nice to have
• Here are some glamour shots you can use if you see a good fit for any of them: https://www.filquarry.net/sh/q7mzkx31rwp8tnb/BXK4Pqwertz_LM9nVwYdQaHfZ?dl=0

```html
<!DOCTYPE html>
<html lang="en">
<head>
<meta charset="utf-8">
<title>Pixora Media Kit – DOOH Now</title>
<link href="https://fonts.googleapis.com/css2?family=Roboto:wght@300;400;700&display=swap" rel="stylesheet">
<style>
:root{
  --page:#e6e7e8;
  --panel:#ffffff;
  --brand-deep:#0592cd;
  --brand-icon:#1590e4;
  --brand-mid:#34a7d8;
  --brand-light:#85cae6;
  --headline:#5ec0e6;
  --ink:#2b2b2b;
  --ink-soft:#555555;
  --badge-grey:#e2e2e2;
  --page-num:#8a8a8a;
}
*{box-sizing:border-box;margin:0;padding:0}
html,body{width:1200px;height:724px;overflow:hidden;background:var(--page);font-family:'Roboto',Arial,sans-serif;color:var(--ink)}
.sheet{position:relative;width:1200px;height:724px}
.panel{position:absolute;width:544px;height:306px;background:var(--panel);overflow:hidden}
.panel--bar{left:39px;top:41px}
.panel--arena{left:617px;top:41px}
.panel--airport{left:39px;top:378px}
.panel--partners{left:617px;top:378px}

.title{position:absolute;left:27px;top:30px;font-weight:300;font-size:18.5px;line-height:23px;color:var(--ink)}
.title strong{font-weight:700}
.title .kicker{display:block;font-weight:700;font-size:17.5px;color:var(--headline);margin-bottom:3px}
.panel--arena .title{left:315px}

.photo{position:absolute;top:0;height:306px}
.photo--bar{left:256px;width:288px;border-radius:50px 0 0 60px/70px 0 0 70px;
  background:linear-gradient(180deg,#6b4a2c 0%,#a0703f 22%,#d89a4e 42%,#7c5a3a 62%,#3a2a1f 100%)}
.photo--arena{left:0;width:291px;border-radius:0 50px 60px 0/0 70px 70px 0;
  background:linear-gradient(180deg,#3a3330 0%,#23283a 30%,#3c4a66 55%,#c9ccd6 78%,#2b2a33 100%)}
.photo--airport{left:254px;width:290px;border-radius:50px 0 0 60px/70px 0 0 70px;
  background:linear-gradient(100deg,#5a3a1e 0%,#a87a48 30%,#e0c8a0 50%,#8a5e34 72%,#4a2f18 100%)}

.bubble{position:absolute;width:71px;height:71px;margin:-35.5px 0 0 -35.5px;border-radius:50%;
  background:var(--brand-light);color:#fff;display:flex;flex-direction:column;align-items:center;justify-content:center;
  font-weight:300;font-size:8.5px;line-height:11px;text-align:center}
.bubble svg{width:28px;height:20px;margin-bottom:3px}

.stat{position:absolute;width:80px;margin-left:-40px;text-align:center}
.stat__icon{width:49px;height:49px;margin:0 auto;border-radius:50%;background:var(--brand-icon);display:flex;align-items:center;justify-content:center}
.stat__icon svg{width:27px;height:27px}
.stat__label{margin-top:6px;font-weight:300;font-size:7.5px;line-height:9px;color:var(--ink-soft)}

.exclusive{position:absolute;width:52px;height:52px;margin:-26px 0 0 -26px;border-radius:50%;background:var(--badge-grey);
  display:flex;align-items:center;justify-content:center}
.exclusive span{transform:rotate(-32deg);color:#fff;font-size:8px;line-height:9px;text-align:center;font-weight:300}

.brandmark{position:absolute;right:11px;bottom:8px;display:flex;align-items:center;gap:3px;font-weight:700;font-size:7.5px;color:#fff}
.brandmark i{display:block;width:8px;height:8px;border-radius:1.5px;background:currentColor}
.brandmark--blue{color:var(--brand-deep)}

.partners__title{position:absolute;left:21px;top:28px;font-weight:300;font-size:19.5px;color:var(--ink)}
.partners__title .kicker{font-weight:700;color:var(--headline)}
.partners__title strong{font-weight:700}
.col-head{position:absolute;font-weight:300;font-size:10px;line-height:12.5px;color:var(--ink)}
.col-head strong{font-weight:700}
.publisher{position:absolute;top:118px;display:flex;align-items:center;gap:5px;font-weight:700;font-size:12px;color:var(--ink)}
.publisher i{display:block;width:18px;height:18px;border-radius:50%;background:var(--brand-mid)}
.quote{position:absolute;top:162px;width:94px;font-weight:300;font-size:7px;line-height:8.9px;color:var(--ink-soft)}
.quote cite{display:block;margin-top:9px;font-style:normal}
.divider{position:absolute;left:260px;top:75px;width:1px;height:187px;background:#d6d6d6}
.brand{position:absolute;left:276px;font-weight:700;font-size:11px;color:var(--ink)}
.page-num{position:absolute;right:14px;bottom:2px;font-weight:700;font-size:38px;color:var(--page-num)}
</style>
</head>
<body>
<main class="sheet">

  <section class="panel panel--bar">
    <h2 class="title"><span class="kicker">DOOH NOW |</span>Inventory Highlights –<br><strong>Bar/Restaurant</strong></h2>
    <div class="photo photo--bar" role="img" aria-label="Sports bar interior with wood-beamed ceiling and wall screens showing motocross">
      <div class="brandmark"><i></i>Pixora</div>
    </div>
    <div class="bubble" style="left:255px;top:152px">
      <svg viewBox="0 0 28 20" fill="none" stroke="#fff" stroke-width="1.6"><rect x="1" y="1" width="26" height="18" rx="1"/><line x1="14" y1="1" x2="14" y2="19"/><circle cx="14" cy="10" r="3.5"/><rect x="1" y="6" width="4" height="8"/><rect x="23" y="6" width="4" height="8"/></svg>
      Sports<br>Fans
    </div>
    <div class="stat" style="left:59px;top:130px">
      <div class="stat__icon"><svg viewBox="0 0 28 28" fill="none" stroke="#fff" stroke-width="2"><rect x="10" y="10" width="8" height="8"/><path d="M3 9V3h6M3 3l5 5M25 9V3h-6M25 3l-5 5M3 19v6h6M3 25l5-5M25 19v6h-6M25 25l-5-5"/></svg></div>
      <p class="stat__label">Massive<br>scale</p>
    </div>
    <div class="stat" style="left:127px;top:130px">
      <div class="stat__icon"><svg viewBox="0 0 28 28" fill="none" stroke="#fff" stroke-width="2"><rect x="3" y="3" width="22" height="22" rx="2"/><path d="M11 9l8 5-8 5z"/></svg></div>
      <p class="stat__label">X screen</p>
    </div>
    <div class="stat" style="left:59px;top:211px">
      <div class="stat__icon"><svg viewBox="0 0 28 28" fill="none" stroke="#fff" stroke-width="2"><path d="M2 12c3-5 7-7 11-7s8 2 11 7c-3 5-7 7-11 7"/><circle cx="13" cy="12" r="3"/><circle cx="20" cy="17" r="3"/><path d="M14 26c0-4 3-5 6-5s6 1 6 5z"/></svg></div>
      <p class="stat__label">X impressions<br>per month</p>
    </div>
    <div class="stat" style="left:127px;top:211px">
      <div class="stat__icon"><svg viewBox="0 0 28 28" fill="none" stroke="#fff" stroke-width="2"><path d="M14 26s-9-8-9-14a9 9 0 0118 0c0 6-9 14-9 14z"/><circle cx="14" cy="12" r="5"/><path d="M10 10c2 0 3 2 5 1M13 17c0-2 2-3 3-4"/></svg></div>
      <p class="stat__label">Nationwide</p>
    </div>
    <div class="exclusive" style="left:194px;top:235px"><span>Exclusive<br>to<br>Pixora</span></div>
  </section>

  <section class="panel panel--arena">
    <div class="photo photo--arena" role="img" aria-label="Packed hockey arena seen from upper seats with center-hung scoreboard"></div>
    <h2 class="title"><span class="kicker">DOOH NOW |</span>Inventory Highlights –<br>Sports <strong>Arenas</strong></h2>
    <div class="bubble" style="left:291px;top:154px">
      <svg viewBox="0 0 28 20" fill="none" stroke="#fff" stroke-width="1.6"><rect x="1" y="1" width="26" height="18" rx="1"/><line x1="14" y1="1" x2="14" y2="19"/><circle cx="14" cy="10" r="3.5"/><rect x="1" y="6" width="4" height="8"/><rect x="23" y="6" width="4" height="8"/></svg>
      Sports<br>Fans
    </div>
    <div class="stat" style="left:385px;top:131px">
      <div class="stat__icon"><svg viewBox="0 0 28 28" fill="none" stroke="#fff" stroke-width="2"><rect x="3" y="3" width="22" height="22" rx="2"/><path d="M11 9l8 5-8 5z"/></svg></div>
      <p class="stat__label">X screens</p>
    </div>
    <div class="stat" style="left:461px;top:131px">
      <div class="stat__icon"><svg viewBox="0 0 28 28" fill="none" stroke="#fff" stroke-width="2"><path d="M2 12c3-5 7-7 11-7s8 2 11 7c-3 5-7 7-11 7"/><circle cx="13" cy="12" r="3"/><circle cx="20" cy="17" r="3"/><path d="M14 26c0-4 3-5 6-5s6 1 6 5z"/></svg></div>
      <p class="stat__label">X impressions<br>per month</p>
    </div>
    <div class="exclusive" style="left:347px;top:230px"><span>Exclusive<br>to<br>Pixora</span></div>
    <div class="stat" style="left:422px;top:205px">
      <div class="stat__icon"><svg viewBox="0 0 28 28" fill="none" stroke="#fff" stroke-width="2"><path d="M14 26s-9-8-9-14a9 9 0 0118 0c0 6-9 14-9 14z"/><circle cx="14" cy="12" r="5"/><path d="M10 10c2 0 3 2 5 1M13 17c0-2 2-3 3-4"/></svg></div>
      <p class="stat__label">Northeast U.S.</p>
    </div>
    <div class="brandmark brandmark--blue"><i></i>Pixora</div>
  </section>

  <section class="panel panel--airport">
    <h2 class="title"><span class="kicker">DOOH NOW |</span>Inventory Highlights –<br>Private <strong>Airports</strong></h2>
    <div class="photo photo--airport" role="img" aria-label="Private airport lounge with chandelier, wood panelling and a wall-mounted screen">
      <div class="brandmark"><i></i>Pixora</div>
    </div>
    <div class="bubble" style="left:252px;top:155px">Exclusive to<br>Pixora</div>
    <div class="stat" style="left:59px;top:131px">
      <div class="stat__icon"><svg viewBox="0 0 28 28" fill="none" stroke="#fff" stroke-width="2"><rect x="3" y="3" width="22" height="22" rx="2"/><path d="M11 9l8 5-8 5z"/></svg></div>
      <p class="stat__label">X screens</p>
    </div>
    <div class="stat" style="left:135px;top:131px">
      <div class="stat__icon"><svg viewBox="0 0 28 28" fill="none" stroke="#fff" stroke-width="2"><path d="M2 12c3-5 7-7 11-7s8 2 11 7c-3 5-7 7-11 7"/><circle cx="13" cy="12" r="3"/><circle cx="20" cy="17" r="3"/><path d="M14 26c0-4 3-5 6-5s6 1 6 5z"/></svg></div>
      <p class="stat__label">X impressions<br>per month</p>
    </div>
    <div class="stat" style="left:95px;top:205px">
      <div class="stat__icon"><svg viewBox="0 0 28 28" fill="none" stroke="#fff" stroke-width="2"><path d="M14 26s-9-8-9-14a9 9 0 0118 0c0 6-9 14-9 14z"/><circle cx="14" cy="12" r="5"/><path d="M10 10c2 0 3 2 5 1M13 17c0-2 2-3 3-4"/></svg></div>
      <p class="stat__label">Nationwide</p>
    </div>
    <div class="exclusive" style="left:173px;top:229px"><span>Exclusive<br>to<br>Pixora</span></div>
  </section>

  <section class="panel panel--partners">
    <h2 class="partners__title"><span class="kicker">DOOH NOW |</span> Our partners speak <strong>volumes</strong></h2>
    <p class="col-head" style="left:46px;top:78px">DOOH Publishers<br><strong>love us</strong></p>
    <div class="publisher" style="left:46px"><i></i>Medirex</div>
    <div class="publisher" style="left:154px">Stadia Screens</div>
    <blockquote class="quote" style="left:46px">“Pixora powers our screen network within Pillwell pharmacies across Canada...we were able to serve 10M impressions through Pixora last year, which is huge for us...Pixora’s technology is so seamless, we just sit back and watch the revenue roll in.<cite>”Leon Varga, GM</cite></blockquote>
    <blockquote class="quote" style="left:154px">“As we have grown our network to nearly 300 digital displays in over 100 sports arenas; Pixora has been a tremendous business partner. I highly recommend Pixora as the solution for anyone looking to build a screen network.”<cite>Brian Fenwick,<br>Co-founder and CEO</cite></blockquote>
    <div class="divider"></div>
    <p class="col-head" style="left:273px;top:78px"><strong>Brands</strong> we’ve<br>worked with</p>
    <p class="brand" style="top:128px">Goldburger</p>
    <p class="brand" style="top:163px">Playvolt</p>
    <p class="brand" style="top:197px">Dashbite</p>
    <p class="brand" style="top:233px">Roadmark</p>
  </section>

  <div class="page-num">4</div>
</main>
</body>
</html>
```